New Website

New website is to be the same as Veltora.

Website needs to be fully functional, with only text and logo to be added by client at a later date.

Logo has been added for reference.

```html
<!DOCTYPE html>
<html lang="en">
<head>
<meta charset="utf-8">
<title>Veltora – The Right Expert, Right Now</title>
<link href="https://fonts.googleapis.com/css2?family=Open+Sans:ital,wght@0,400;0,600;0,700;1,400;1,600&display=swap" rel="stylesheet">
<style>
:root{
  --blue:#3b72bd;
  --blue-dark:#2c5e9f;
  --band:#4d7ec3;
  --footer:#4676bb;
  --footer-bar:#34609d;
  --ink:#333a44;
  --muted:#6b7280;
  --grey-band:#ebedf0;
  --card:#e9ebee;
  --white:#fff;
}
*{box-sizing:border-box;margin:0;padding:0}
html,body{width:1200px;height:3032px;overflow:hidden}
body{font-family:"Open Sans",Arial,sans-serif;color:var(--ink);background:var(--white);position:relative}
.section-title{font-size:26px;font-weight:600;letter-spacing:1px;text-align:center;color:#4a5260;text-transform:uppercase}
.btn{display:inline-block;font-size:14px;font-weight:600;letter-spacing:1px;text-transform:uppercase;padding:12px 26px}
.btn-outline{border:2px solid var(--blue);color:var(--blue);background:var(--white)}

/* header */
.site-header{position:absolute;top:0;left:0;width:1200px;height:64px;display:flex;align-items:center;padding:0 80px;background:var(--white);z-index:2}
.brand{display:flex;align-items:center;gap:10px}
.brand-mark{width:26px;height:26px;border-radius:50%;background:var(--blue)}
.brand-name{font-size:26px;font-weight:600;letter-spacing:3px;color:var(--blue)}
.main-nav{margin-left:auto;display:flex;align-items:center;gap:28px;font-size:13px;font-weight:600;color:#444;text-transform:uppercase}
.main-nav .sign{color:var(--blue)}
.main-nav .cta{border:2px solid var(--blue);color:var(--blue);padding:8px 14px}

/* hero */
.hero{position:absolute;top:64px;left:0;width:1200px;height:476px;background:linear-gradient(90deg,#dfe6ee 0%,#c9d3de 45%,#b7c2cf 70%,#d6dbe2 100%)}
.hero-photo{position:absolute;right:0;top:0;width:620px;height:476px;background:linear-gradient(90deg,rgba(0,0,0,0),#a7b2c0 35%,#8e99a8 70%,#c4ccd6)}
.hero-copy{position:absolute;left:80px;top:40px;width:560px}
.hero-copy h1{font-size:64px;line-height:1.08;font-weight:600;color:var(--blue-dark)}
.hero-copy h1 sup{font-size:24px}
.hero-copy p{margin-top:22px;font-size:26px;line-height:1.3;color:var(--white);text-shadow:0 1px 2px rgba(0,0,0,.25)}
.hero .btn{position:absolute;left:80px;top:340px;background:var(--blue);color:var(--white)}
.dots{position:absolute;left:80px;top:440px;display:flex;gap:10px}
.dots span{width:12px;height:12px;border-radius:50%;background:rgba(60,70,90,.5)}
.dots span:first-child{background:#3a4250}

/* welcome */
.welcome{position:absolute;top:590px;left:80px;width:1040px;text-align:center}
.welcome p{margin-top:26px;font-size:13px;line-height:1.75;color:var(--muted)}

/* testimonials */
.testimonials{position:absolute;top:734px;left:0;width:1200px;height:246px;background:var(--grey-band);text-align:center}
.testimonials .section-title{margin-top:36px}
.testimonials blockquote{width:960px;margin:26px auto 0;font-size:13px;line-height:1.75;color:var(--muted)}
.testimonials .who{margin-top:14px;font-size:13px;font-weight:600;color:#444}
.testimonials .role{font-size:12px;color:var(--muted)}
.arrow{position:absolute;top:112px}
.arrow.prev{left:70px}.arrow.next{right:70px}

/* video */
.watch{position:absolute;top:1030px;left:0;width:1200px}
.video{position:absolute;top:102px;left:72px;width:1056px;height:356px;background:linear-gradient(180deg,#2b2f36,#14171c 60%,#23272e)}
.video .play{position:absolute;left:478px;top:118px}
.video .btn{position:absolute;left:482px;top:288px;border:1px solid #fff;color:#fff;font-size:11px;padding:6px 14px}

/* experts */
.experts{position:absolute;top:1532px;left:0;width:1200px;height:590px;background:var(--band);color:var(--white);text-align:center}
.experts .section-title{color:var(--white);margin-top:46px}
.expert{position:absolute;top:100px;width:240px}
.expert .photo{height:240px;background:linear-gradient(180deg,#e6e9ed,#b9c1cb)}
.expert .label{height:48px;background:#355f9a;text-align:left;padding:6px 12px}
.expert .label b{display:block;font-size:15px;font-weight:600}
.expert .label i{font-size:11px;font-style:italic;opacity:.85}
.experts .blurb{position:absolute;top:424px;left:80px;width:1040px;font-size:15px;font-style:italic;line-height:1.6;text-align:left}
.experts .btn{position:absolute;top:526px;left:528px;border:2px solid #fff;color:#fff;font-size:12px;padding:8px 18px}

/* how it works */
.how{position:absolute;top:2176px;left:0;width:1200px;text-align:center}
.how .lead{margin-top:10px;font-size:16px;color:var(--muted)}
.step{position:absolute;top:76px;width:240px;height:336px;background:var(--card);text-align:center}
.step svg{margin-top:30px}
.step h3{font-size:17px;font-weight:600;color:var(--blue-dark);line-height:1.25;margin-top:34px;padding:0 18px}
.step p{font-size:12px;line-height:1.5;color:var(--muted);padding:8px 24px 0}
.how .btn{position:absolute;top:432px;left:522px;font-size:12px;padding:8px 18px}

/* footer */
.site-footer{position:absolute;top:2692px;left:0;width:1200px;height:288px;background:var(--footer);color:var(--white);font-size:12px}
.foot-links{position:absolute;left:80px;top:24px;list-style:none;font-size:16px;line-height:2.4}
.foot-news{position:absolute;left:348px;top:24px;width:320px}
.foot-news h4,.foot-help h4{font-size:16px;font-weight:600}
.news-item{margin-top:12px;display:flex;gap:8px;line-height:1.5;opacity:.95}
.news-item .q{font-size:22px;line-height:1}
.news-item small{display:block;opacity:.8;margin-top:2px}
.foot-help{position:absolute;left:702px;top:24px;width:320px;line-height:1.5}
.foot-help p{margin-top:10px}
.foot-help h4.contact{margin-top:18px}
.footer-bar{position:absolute;top:2980px;left:0;width:1200px;height:52px;background:var(--footer-bar);color:#dfe7f3;font-size:11px;display:flex;align-items:center;padding:0 80px}
.social{margin-left:auto;display:flex;gap:8px}
.social span{width:22px;height:22px;border-radius:50%;background:#cbd8ea}
</style>
</head>
<body>

<header class="site-header">
  <div class="brand"><span class="brand-mark"></span><span class="brand-name">VELTORA</span></div>
  <nav class="main-nav">
    <span>Home</span><span>How it Works</span><span>Products</span><span>Blog</span><span>Help</span>
    <span class="sign">Sign In | Register</span>
    <span class="cta">Make an Expert</span>
  </nav>
</header>

<section class="hero">
  <div class="hero-photo" role="img" aria-label="Photo of a smiling businesswoman in an office"></div>
  <div class="hero-copy">
    <h1>The Right Expert, Right Now<sup>™</sup></h1>
    <p>Aliquam molestie, mi et imperdiet euismod, dui purus auctor tellus, et interdum lacus lectus et ante.</p>
  </div>
  <span class="btn">Watch the Video</span>
  <div class="dots"><span></span><span></span><span></span><span></span></div>
</section>

<section class="welcome">
  <h2 class="section-title">Welcome to Our Website</h2>
  <p>Aliquam molestie, mi et imperdiet euismod, dui purus auctor tellus, et interdum lacus lectus et ante. Sed accumsan sollicitudin sapien, sit amet adipiscing ligula gravida at. In congue neque ac dolor vehicula volutpat. Nam tincidunt sem non nisl. Sed sollicitudin quam vel nulla. Sed porta risus sed erat sagittis dapibus. Praesent aliquam blandit est, ac lobortis metus facilisis non. Vivamus luctus in magna varius commodo. Sed semper massa, et feugiat lorem tempor vitae.</p>
</section>

<section class="testimonials">
  <h2 class="section-title">What Client Are Saying</h2>
  <blockquote>Aliquam molestie, mi et imperdiet euismod, dui purus auctor tellus, et interdum lacus lectus et ante. Sed accumsan sollicitudin sapien, sit amet adipiscing ligula gravida at. In congue neque ac dolor vehicula volutpat. Nam tincidunt sem non nisl. Sed sollicitudin quam vel nulla viverra, nec consequat orci ultrices. Aenean ultricies dui vitae augue fringilla, in pharetra mi hendrerit.</blockquote>
  <div class="who">Marlow Hensley</div>
  <div class="role">– CEO, Brookfield, NY</div>
  <svg class="arrow prev" width="14" height="24" viewBox="0 0 14 24"><path d="M12 2 2 12l10 10" fill="none" stroke="#555" stroke-width="2.5"/></svg>
  <svg class="arrow next" width="14" height="24" viewBox="0 0 14 24"><path d="m2 2 10 10L2 22" fill="none" stroke="#555" stroke-width="2.5"/></svg>
</section>

<section class="watch">
  <h2 class="section-title">Watch a Video</h2>
  <div class="video" role="img" aria-label="Video still of a chalkboard with handwritten words about asking an expert">
    <svg class="play" width="100" height="100" viewBox="0 0 100 100"><circle cx="50" cy="50" r="46" fill="none" stroke="#fff" stroke-width="5"/><path d="M40 30v40l30-20z" fill="#fff"/></svg>
    <span class="btn">Watch the Video</span>
  </div>
</section>

<section class="experts">
  <h2 class="section-title">Introducing Your Business Expert Network</h2>
  <div class="expert" style="left:80px"><div class="photo" role="img" aria-label="Portrait photo of an expert"></div><div class="label"><b>Name Heading Here</b><i>Partner</i></div></div>
  <div class="expert" style="left:348px"><div class="photo" role="img" aria-label="Portrait photo of an expert"></div><div class="label"><b>Name Heading Here</b><i>Partner</i></div></div>
  <div class="expert" style="left:612px"><div class="photo" role="img" aria-label="Portrait photo of an expert"></div><div class="label"><b>Name Heading Here</b><i>Partner</i></div></div>
  <div class="expert" style="left:880px"><div class="photo" role="img" aria-label="Portrait photo of an expert"></div><div class="label"><b>Name Heading Here</b><i>Partner</i></div></div>
  <p class="blurb">All of our experts meet high qualification requirements and undergo rigorous testing for their specific skills and consulting abilities. Learn more about how experts are chosen. If you think you have what it takes, become an expert today.</p>
  <span class="btn">See All Experts</span>
</section>

<section class="how">
  <h2 class="section-title">How It Works</h2>
  <p class="lead">Find an Expert who's just right for your business need. Your Expert Package includes:</p>

  <div class="step" style="left:80px">
    <svg width="130" height="130" viewBox="0 0 130 130"><circle cx="52" cy="52" r="34" fill="none" stroke="#3b72bd" stroke-width="14"/><path d="m78 78 36 36" stroke="#3b72bd" stroke-width="18" stroke-linecap="round"/></svg>
    <h3>Pre Session Discovery</h3>
    <p>We review details about your business, your challenge, and your goals.</p>
  </div>
  <div class="step" style="left:348px">
    <svg width="130" height="130" viewBox="0 0 130 130"><rect x="14" y="18" width="102" height="74" rx="4" fill="none" stroke="#3b72bd" stroke-width="8"/><rect x="46" y="40" width="38" height="30" rx="3" fill="#3b72bd"/><path d="M50 104h30M65 92v12" stroke="#3b72bd" stroke-width="8"/></svg>
    <h3>One-On-One Session</h3>
    <p>You meet your expert live for your session, focused on your goals from the first minute.</p>
  </div>
  <div class="step" style="left:612px">
    <svg width="130" height="130" viewBox="0 0 130 130"><rect x="28" y="12" width="74" height="104" rx="4" fill="none" stroke="#3b72bd" stroke-width="8"/><path d="m40 38 6 6 10-12M40 62l6 6 10-12M40 86l6 6 10-12" fill="none" stroke="#3b72bd" stroke-width="5"/><path d="M64 40h26M64 64h26M64 88h26" stroke="#3b72bd" stroke-width="6"/></svg>
    <h3>Session Summary Report</h3>
    <p>The Expert delivers a report that includes summary details.</p>
  </div>
  <div class="step" style="left:880px">
    <svg width="130" height="130" viewBox="0 0 130 130"><path d="M100 18c-30 4-48 24-58 50l20 20c26-10 46-28 50-58z" fill="#3b72bd"/><circle cx="82" cy="46" r="9" fill="#e9ebee"/><path d="M42 68 22 64l16-20h20zM62 88l4 20 20-16V72z" fill="#3b72bd"/><path d="M36 86 18 112l26-18" fill="#3b72bd"/></svg>
    <h3>Post-Session Options</h3>
    <p>Continue your relationship with the Expert or get more help with Veltora's support.</p>
  </div>
  <span class="btn btn-outline">See How It Works</span>
</section>

<footer class="site-footer">
  <ul class="foot-links"><li>About Us</li><li>Our Team</li><li>Legal</li><li>Contact Us</li></ul>
  <div class="foot-news">
    <h4>What We're Thinking</h4>
    <div class="news-item"><span class="q">“</span><div>Aliquam molestie, mi et imperdiet euismod, dui purus auctor tellus, et interdum lacus lectus et ante. Sed accumsan sapien.<small>Jan 12, 2015</small></div></div>
    <div class="news-item"><span class="q">“</span><div>Aliquam molestie, mi et imperdiet euismod, dui purus auctor tellus, et interdum lacus lectus et ante. Sed accumsan sapien.<small>Jan 12, 2015</small></div></div>
  </div>
  <div class="foot-help">
    <h4>Need Help?</h4>
    <p>Aliquam molestie, mi et imperdiet euismod, dui purus auctor tellus, et interdum lacus lectus et ante. Sed accumsan sollicitudin sapien.</p>
    <h4 class="contact">Contact Us</h4>
    <p>Veltora<br>hello@veltora-experts.com</p>
  </div>
</footer>
<div class="footer-bar">
  <span>Copyright © 2015, CompanyName. All Right Reserved.</span>
  <div class="social"><span></span><span></span><span></span><span></span><span></span></div>
</div>

</body>
</html>
```